Web Design Project for Communications Agency

The design I need (PSD file) is for an agency offering specialised PR and communications services for customers in the healthcare sector.

OBJECTIVES OF THE WEBSITE:
1. To promote the agency's communication services
2. To position Solène Brivard as an industry leader, an expert in healthcare PR and communications by highlighting blogposts and social media.

WHAT I NEED:
1st, I need the design for the Home Page ONLY.
Once approved, I will need the other pages designed as well. (Here is prototype that we've already developed for the Website that will guide you in the design:
http://qorvelle.net/solenebrivard/)

VISUAL INSPIRATION
We want to give this Website a "Flat Design" look. Here are some websites for inspiration :
- http://tavrolinkworks.com/#!/process
- http://www.brindlemoss.co/
- http://quellaroft.com/

Also, reuse images found on the company's current Website :
http://www.solenebrivard.com/fr/index.html

HOMEPAGE MAIN ELEMENTS:
1. Main menu : 6 sections
Accueil | Agence | Services | Approche | Publications | Contact

2. Main Call To Action (big dark rectangle in prototype):
Can be slider or just an information bloc.

3. Publications récentes :
The 4 latest blog posts must be features on the homepage (will be linked with the "Publications" section)

4. Dynamic Footer :
Contains a Twitter feed and a Subscribe to our Newsletter feature (revecez nos publications)

OTHER PAGES (to design once Homepage is approved)
- Agence (about us)
- Services (our team)
- Approche (our approach)
- Publications (blog articles)
- Contact (Contact us)

Industry/Entity Type

Communications

Requirements
Must have
• Please refer to prototype :
http://qorvelle.net/solenebrivard/
Must have ALL features present in prototype.

Also, must reuse this picture in the design : http://solenebrivard.com/static/images/home-big-box.jpg

Finally, you will find attached the company logo.

```html
<!DOCTYPE html>
<html lang="fr">
<head>
<meta charset="utf-8">
<title>Solène Brivard — Conseil santé</title>
<link rel="stylesheet" href="https://fonts.googleapis.com/css2?family=Open+Sans:wght@400;600;700&family=Gelasio:ital,wght@0,400;0,600;1,400&display=swap">
<style>
:root{
  --red:#d0141c;
  --red-dark:#a50e14;
  --header-bg:#efefef;
  --section-bg:#e9e9e9;
  --card-bg:#ffffff;
  --ink:#333333;
  --muted:#666666;
  --soft:#a9a9a9;
  --tweet-blue:#2aa3e0;
  --footer-bg:#222222;
  --footer-text:#8a8a8a;
  --icon-grey:#9a9a9a;
}
*{box-sizing:border-box;margin:0;padding:0}
html,body{width:1200px;height:2329px;overflow:hidden}
body{position:relative;font-family:"Open Sans",Arial,sans-serif;color:var(--ink);background:var(--section-bg)}
a{text-decoration:none;color:inherit}

/* Header */
.site-header{position:absolute;left:0;top:0;width:1200px;height:106px;background:var(--header-bg);border-bottom:1px solid #dcdcdc}
.brand{position:absolute;left:112px;top:30px;display:flex;align-items:center;gap:12px;font-size:34px;font-weight:600;color:var(--red);letter-spacing:-.5px}
.brand-mark{width:20px;height:20px;background:var(--red)}
.social-top{position:absolute;left:815px;top:12px;display:flex;gap:8px}
.social-top span{width:24px;height:24px;border-radius:50%;background:var(--icon-grey)}
.lang-select{position:absolute;left:981px;top:12px;width:93px;height:20px;border:1px solid #888;background:#fff;font-size:12px;line-height:18px;padding-left:5px;color:#444}
.lang-select::before{content:"";position:absolute;right:24px;top:5px;width:14px;height:9px;background:#26418f}
.lang-select::after{content:"";position:absolute;right:0;top:0;width:18px;height:18px;border-left:1px solid #888;background:linear-gradient(#fff,#ddd)}
.main-nav{position:absolute;left:495px;top:56px;width:592px;height:34px;background:linear-gradient(#e11c24,var(--red-dark));border-radius:3px;display:flex;box-shadow:0 2px 3px rgba(0,0,0,.2)}
.main-nav a{flex:1 1 auto;color:#fff;font-size:12.5px;text-transform:uppercase;text-align:center;line-height:34px;border-right:1px solid rgba(0,0,0,.2)}
.main-nav a:last-child{border-right:0}

/* Hero */
.hero{position:absolute;left:0;top:106px;width:1200px;height:540px;background:radial-gradient(ellipse at 60% 40%,#5a3a2a 0%,#3a2519 45%,#1d140f 100%)}
.hero-title{position:absolute;left:147px;top:146px;width:640px;color:#fff;font-size:33px;font-weight:600;line-height:42px}
.hero-cta{position:absolute;left:146px;top:299px;width:287px;height:70px;background:linear-gradient(#fafafa,#dcdcdc);border-radius:3px;box-shadow:0 3px 6px rgba(0,0,0,.5);display:flex;align-items:center}
.hero-cta-icon{width:42px;height:42px;background:var(--red);display:flex;align-items:center;justify-content:center;border-radius:2px}
.hero-cta-label{margin-left:18px;font-size:25px;font-weight:700;color:#3c3c3c}

/* Publications */
.publications{position:absolute;left:0;top:646px;width:1200px;height:1224px;background:var(--section-bg)}
.section-tab{position:absolute;left:124px;top:51px;width:352px;height:71px;background:#fff;box-shadow:0 1px 3px rgba(0,0,0,.15);display:flex;align-items:center;padding-left:18px;gap:16px;font-size:28px;font-weight:600;color:#333}
.section-tab::after{content:"";position:absolute;left:22px;bottom:-12px;border-left:12px solid transparent;border-right:12px solid transparent;border-top:12px solid #fff}
.post-list{position:absolute;left:121px;top:149px;width:961px;background:var(--card-bg);box-shadow:0 1px 4px rgba(0,0,0,.15)}
.post{position:relative;height:346px;border-bottom:1px solid #ececec}
.post:nth-child(2){height:320px}
.post:last-child{border-bottom:0;height:344px}
.post-media{position:absolute;top:0;height:100%}
.post-body{position:absolute;top:34px;width:410px}
.post-title{font-family:"Gelasio",Georgia,serif;font-weight:400;font-size:17px;color:#222}
.post-date{display:inline-block;margin-top:8px;padding:2px 6px;background:#f1f1f1;font-family:"Gelasio",Georgia,serif;font-style:italic;font-size:15px;color:#333}
.post-excerpt{margin-top:20px;font-size:12.4px;line-height:18px;color:var(--muted)}
.post-link{display:inline-flex;align-items:center;gap:10px;margin-top:28px;height:35px;padding:0 16px;background:#f1f1f1;color:var(--red);font-size:13.5px}

/* Twitter band */
.tweet-band{position:absolute;left:0;top:1870px;width:1200px;height:190px;background:#fff;text-align:center}
.tweet-badge{position:absolute;left:571px;top:-39px;width:56px;height:56px;border-radius:50%;background:#fff}
.tweet-badge span{position:absolute;left:14px;top:14px;width:28px;height:28px;border-radius:50%;background:var(--tweet-blue)}
.tweet-text{position:absolute;left:150px;top:37px;width:900px;font-size:25px;line-height:32px;color:var(--soft)}
.tweet-text em{font-style:normal;color:var(--tweet-blue)}
.tweet-follow{position:absolute;left:0;top:123px;width:1200px;font-size:22px;font-weight:600;letter-spacing:-.3px;color:#333}

/* Footer */
.site-footer{position:absolute;left:0;top:2060px;width:1200px;height:269px;background:var(--footer-bg);color:var(--footer-text)}
.footer-heading{font-size:15px;font-weight:600;color:#fff;text-transform:uppercase}
.footer-links{position:absolute;left:113px;top:23px}
.footer-links ul{list-style:none;margin-top:16px}
.footer-links li{font-size:12.5px;line-height:22px}
.footer-contact{position:absolute;left:313px;top:23px}
.footer-contact p{margin-top:16px;font-size:12.5px;line-height:22px;text-transform:uppercase}
.footer-contact p span{text-transform:none}
.newsletter{position:absolute;left:799px;top:28px;width:273px}
.newsletter-field{display:block;margin-top:10px;width:273px;height:34px;background:#fff;border-radius:3px;padding-left:12px;font-size:14px;line-height:34px;color:#999}
.newsletter-field:first-of-type{margin-top:16px}
.newsletter-submit{margin-top:11px;width:159px;height:33px;background:var(--red);color:#fff;font-size:14.5px;font-weight:600;line-height:33px;text-align:center}
.footer-rule{position:absolute;left:113px;top:206px;width:960px;height:1px;background:#3a3a3a}
.copyright{position:absolute;left:113px;top:228px;font-size:12.5px}
.social-bottom{position:absolute;left:798px;top:221px;display:flex;gap:8px}
.social-bottom span{width:30px;height:30px;border-radius:50%;background:#d8d8d8}
</style>
</head>
<body>

<header class="site-header">
  <a class="brand" href="#"><span class="brand-mark"></span>Solène Brivard</a>
  <div class="social-top"><span></span><span></span><span></span><span></span><span></span></div>
  <div class="lang-select">English</div>
  <nav class="main-nav">
    <a href="#">Accueil</a><a href="#">Agence</a><a href="#">Services</a><a href="#">Approche</a><a href="#">Publications</a><a href="#">Contact</a>
  </nav>
</header>

<section class="hero" role="img" aria-label="Photo d'une salle de conférence avec des participants assis, tons bruns sombres">
  <h1 class="hero-title">Cabinet-conseil en communications et affaires publiques spécialisé dans le secteur de la santé.</h1>
  <a class="hero-cta" href="#">
    <span class="hero-cta-icon"><svg width="20" height="20" viewBox="0 0 20 20"><path d="M4 4l6 6 6-6M4 10l6 6 6-6" fill="none" stroke="#fff" stroke-width="3"/></svg></span>
    <span class="hero-cta-label">EN SAVOIR PLUS</span>
  </a>
</section>

<main class="publications">
  <h2 class="section-tab">
    <svg width="30" height="30" viewBox="0 0 30 30"><rect x="3" y="2" width="24" height="26" rx="2" fill="#d9d9d9"/><path d="M8 10h14M8 15h14M8 20h10" stroke="#fff" stroke-width="2"/></svg>
    Publication Récentes
  </h2>

  <div class="post-list">
    <article class="post">
      <div class="post-media" role="img" aria-label="Photo d'un homme tendant une carte de visite" style="left:0;width:469px;background:linear-gradient(90deg,#3b4a5c,#7a8796 55%,#c9cdd2)"></div>
      <div class="post-body" style="left:523px">
        <h3 class="post-title">Titre de la publication</h3>
        <span class="post-date">23 juillet 2013</span>
        <p class="post-excerpt">Lorem ipsum dolor sit amet, consectetur adipisicing elit, sed do eiusmod tempor incididunt ut labore et dolore magna aliqua. Ut enim ad minim veniam, quis nostrud exercitation ullamco laboris nisi ut aliquip ex ea commodo consequat. Duis aute irure dolor in reprehenderit in voluptate velit esse cillum dolore eu fugiat nulla pariatur. Excepteur sint occaecat cupidatat non proident, sunt in culpa qui officia deserunt mollit anim id est laborum.</p>
        <a class="post-link" href="#">Article complet <svg width="16" height="16" viewBox="0 0 16 16"><circle cx="8" cy="8" r="6.5" fill="none" stroke="#d0141c" stroke-width="1.5"/><path d="M5 8h6M8.5 5.5L11 8l-2.5 2.5" fill="none" stroke="#d0141c" stroke-width="1.5"/></svg></a>
      </div>
    </article>

    <article class="post">
      <div class="post-body" style="left:29px;top:36px">
        <h3 class="post-title">Titre de la publication</h3>
        <span class="post-date">23 juillet 2013</span>
        <p class="post-excerpt">Lorem ipsum dolor sit amet, consectetur adipisicing elit, sed do eiusmod tempor incididunt ut labore et dolore magna aliqua. Ut enim ad minim veniam, quis nostrud exercitation ullamco laboris nisi ut aliquip ex ea commodo consequat. Duis aute irure dolor in reprehenderit in voluptate velit esse cillum dolore eu fugiat nulla pariatur. Excepteur sint occaecat cupidatat non proident, sunt in culpa qui officia deserunt mollit anim id est laborum.</p>
        <a class="post-link" href="#">Article complet <svg width="16" height="16" viewBox="0 0 16 16"><circle cx="8" cy="8" r="6.5" fill="none" stroke="#d0141c" stroke-width="1.5"/><path d="M5 8h6M8.5 5.5L11 8l-2.5 2.5" fill="none" stroke="#d0141c" stroke-width="1.5"/></svg></a>
      </div>
      <div class="post-media" role="img" aria-label="Illustration d'un cube blanc avec une croix rouge sur le dessus" style="left:647px;width:314px;background:radial-gradient(ellipse at 55% 45%,#f4f4f4,#dcdcdc 70%,#e8e8e8)"></div>
    </article>

    <article class="post">
      <div class="post-media" role="img" aria-label="Photo d'un homme en chemise blanche, bras croisés, devant une équipe de centre d'appels" style="left:0;width:540px;background:linear-gradient(90deg,#b8bfc4,#d7dadc 50%,#ffffff)"></div>
      <div class="post-body" style="left:525px">
        <h3 class="post-title">Titre de la publication</h3>
        <span class="post-date">23 juillet 2013</span>
        <p class="post-excerpt">Lorem ipsum dolor sit amet, consectetur adipisicing elit, sed do eiusmod tempor incididunt ut labore et dolore magna aliqua. Ut enim ad minim veniam, quis nostrud exercitation ullamco laboris nisi ut aliquip ex ea commodo consequat. Duis aute irure dolor in reprehenderit in voluptate velit esse cillum dolore eu fugiat nulla pariatur. Excepteur sint occaecat cupidatat non proident, sunt in culpa qui officia deserunt mollit anim id est laborum.</p>
        <a class="post-link" href="#">Article complet <svg width="16" height="16" viewBox="0 0 16 16"><circle cx="8" cy="8" r="6.5" fill="none" stroke="#d0141c" stroke-width="1.5"/><path d="M5 8h6M8.5 5.5L11 8l-2.5 2.5" fill="none" stroke="#d0141c" stroke-width="1.5"/></svg></a>
      </div>
    </article>
  </div>
</main>

<section class="tweet-band">
  <div class="tweet-badge"><span></span></div>
  <p class="tweet-text">Velit esse cillum dolore eu fugiat nulla pariatur. Excepteur sint occaecat cupidatat non proident. <em>@SoleneBrivard #EnjeuSanté</em></p>
  <p class="tweet-follow">Follow @Veltoria_Rcrt</p>
</section>

<footer class="site-footer">
  <div class="footer-links">
    <h4 class="footer-heading">Links</h4>
    <ul><li>Accueil</li><li>Agence</li><li>Services</li><li>Approche</li><li>Publications</li><li>Contact</li></ul>
  </div>
  <div class="footer-contact">
    <h4 class="footer-heading">Contact us</h4>
    <p>Solène Brivard<br>Conseil santé | Relations publiques<br><span>Tél. : 450.555.0172</span></p>
  </div>
  <form class="newsletter">
    <h4 class="footer-heading">Recevez nos publications</h4>
    <span class="newsletter-field">Votre nom</span>
    <span class="newsletter-field">Votre courriel</span>
    <div class="newsletter-submit">Abonnez-vous</div>
  </form>
  <div class="footer-rule"></div>
  <p class="copyright">(c) Solène Brivard. Tous droits réservés.</p>
  <div class="social-bottom"><span></span><span></span><span></span><span></span><span></span><span></span><span></span></div>
</footer>

</body>
</html>
```